SkyvornQ Business Cards and Stationary Design

Need a design for our business cards and stationary. I want to carry on the theme of the logo. I want the business cards to have a design on the back. I would like the business cards and the stationary to carry the same theme, design scheme, and branding

Target Market(s)

Airlines and Maintenance Facilities

Industry/Entity Type

Aviation

Contact Information for Business Card

Name
Position Title
Address: 4827 Trellis Hollow Road, Harlan Bay, Florida, 34951
Office Number
Mobile Number
Email
Website

Font styles to use
Serif
Sans Serif

Colors

Designer to choose colors to be used in the design.

```html
<!DOCTYPE html>
<html lang="en">
<head>
<meta charset="utf-8">
<title>SkyvornQ Business Card</title>
<link href="https://fonts.googleapis.com/css2?family=Exo+2:wght@700&family=Open+Sans:wght@400;600&display=swap" rel="stylesheet">
<style>
  :root {
    --backdrop: #3a3a3c;
    --card-black: #232427;
    --text-light: #f1f2f4;
    --text-soft: #d6d8dc;
    --brand-steel: #8d9096;
    --sky-blue: #1aa3e8;
    --navy: #12305f;
    --navy-deep: #0d2650;
  }
  * { box-sizing: border-box; margin: 0; padding: 0; }
  html, body { width: 799px; height: 1200px; overflow: hidden; }
  body {
    background: var(--backdrop);
    font-family: "Open Sans", sans-serif;
    display: flex;
    flex-direction: column;
    align-items: center;
    justify-content: space-around;
    padding: 90px 0;
  }
  .card {
    position: relative;
    width: 620px;
    height: 354px;
    border-radius: 28px;
    background: var(--card-black);
    overflow: hidden;
    box-shadow: 0 18px 40px rgba(0,0,0,0.45);
  }
  /* Front */
  .card-front {
    display: flex;
    flex-direction: column;
    align-items: center;
    justify-content: center;
    gap: 22px;
  }
  .brand-circle {
    width: 70px;
    height: 70px;
    border-radius: 50%;
    border: 3px solid var(--brand-steel);
  }
  .brand-name {
    font-family: "Exo 2", sans-serif;
    font-weight: 700;
    letter-spacing: 8px;
    text-transform: uppercase;
    color: var(--brand-steel);
    font-size: 44px;
  }
  /* Back */
  .back-brand {
    position: absolute;
    top: 36px;
    left: 40px;
    display: flex;
    align-items: center;
    gap: 16px;
  }
  .back-brand .brand-name { color: var(--text-light); font-size: 42px; letter-spacing: 7px; }
  .back-brand .brand-circle { width: 46px; height: 46px; border-color: var(--sky-blue); }
  .holder {
    position: absolute;
    top: 112px;
    left: 40px;
  }
  .holder-name { color: var(--text-light); font-weight: 600; font-size: 22px; }
  .holder-title { color: var(--sky-blue); font-size: 13px; margin-top: 1px; }
  .holder-address { color: var(--text-soft); font-size: 13px; line-height: 1.4; margin-top: 10px; }
  .accent-band {
    position: absolute;
    left: 0;
    right: 0;
    bottom: 0;
    height: 118px;
    background: linear-gradient(180deg, var(--navy) 0%, var(--navy-deep) 100%);
    border-top: 4px solid var(--sky-blue);
  }
  .contact-list {
    position: absolute;
    right: 34px;
    bottom: 18px;
    list-style: none;
    text-align: right;
  }
  .contact-list li {
    display: flex;
    align-items: center;
    justify-content: flex-end;
    gap: 9px;
    color: var(--text-light);
    font-size: 14.5px;
    line-height: 22px;
  }
  .contact-list svg { width: 14px; height: 14px; fill: var(--sky-blue); }
</style>
</head>
<body>
  <section class="card card-front">
    <div class="brand-circle"></div>
    <div class="brand-name">SkyvornQ</div>
  </section>

  <section class="card card-back">
    <div class="accent-band" role="img" aria-label="Decorative blue and navy accent band along the bottom of the card"></div>

    <div class="back-brand">
      <div class="brand-name">SkyvornQ</div>
      <div class="brand-circle"></div>
    </div>

    <div class="holder">
      <p class="holder-name">Marcus Delwyn</p>
      <p class="holder-title">Managing Director</p>
      <p class="holder-address">4827 Trellis Hollow Road,<br>Harlan Bay, Florida, 34951</p>
    </div>

    <ul class="contact-list">
      <li>2468 1357 900
        <svg viewBox="0 0 24 24"><path d="M6.6 10.8a15 15 0 0 0 6.6 6.6l2.2-2.2c.3-.3.7-.4 1-.2 1.1.4 2.3.6 3.6.6.6 0 1 .4 1 1V20c0 .6-.4 1-1 1A17 17 0 0 1 3 4c0-.6.4-1 1-1h3.5c.6 0 1 .4 1 1 0 1.3.2 2.5.6 3.6.1.3 0 .7-.2 1z"/></svg></li>
      <li>5550 4321 686
        <svg viewBox="0 0 24 24"><path d="M7 1h10a2 2 0 0 1 2 2v18a2 2 0 0 1-2 2H7a2 2 0 0 1-2-2V3a2 2 0 0 1 2-2zm0 4v13h10V5zm5 14.5a1 1 0 1 0 0 2 1 1 0 0 0 0-2z"/></svg></li>
      <li>marcus@skyvornq.com
        <svg viewBox="0 0 24 24"><path d="M2 5h20v14H2zm2 2v.5l8 5 8-5V7zm0 2.8V17h16V9.8l-8 5z"/></svg></li>
      <li>www.skyvornq.com
        <svg viewBox="0 0 24 24"><path d="M12 2a10 10 0 1 0 0 20 10 10 0 0 0 0-20zm6.9 6h-3a15 15 0 0 0-1.3-3.9A8 8 0 0 1 18.9 8zM12 4c.8 1.2 1.5 2.5 1.9 4h-3.8c.4-1.5 1.1-2.8 1.9-4zM4.3 14a8 8 0 0 1 0-4h3.4a16 16 0 0 0 0 4zm.8 2h3a15 15 0 0 0 1.3 3.9A8 8 0 0 1 5.1 16zm3-8h-3a8 8 0 0 1 4.3-3.9C8.8 5.3 8.4 6.6 8.1 8zM12 20c-.8-1.2-1.5-2.5-1.9-4h3.8c-.4 1.5-1.1 2.8-1.900 4zm2.3-6H9.7a14 14 0 0 1 0-4h4.6a14 14 0 0 1 0 4zm.3 5.9c.6-1.2 1-2.5 1.3-3.9h3a8 8 0 0 1-4.3 3.9zm1.7-5.9a16 16 0 0 0 0-4h3.4a8 8 0 0 1 0 4z"/></svg></li>
    </ul>
  </section>
</body>
</html>
```